Calvanto Group Real Estate Company business cards

New business card design, we are generally happy with the basic layout of the existing front of business card, (feel free to change) but require a head shot photo on the back side.

http://www.calvanto.com.au/

Attached logos, and existing business card

------------------------------

Target Market(s)

Real estate

Industry/Entity Type

Real Estate

Contact Information for Business Card

Standard size double sided

Font styles to use
Other font styles liked:
• Futura

Requirements
Must have
• Photo head shot on the back side
Nice to have
• yes
Should not have
• No

```html
<!DOCTYPE html>
<html lang="en">
<head>
<meta charset="utf-8">
<title>Calvanto Group – Business Cards</title>
<link rel="stylesheet" href="https://fonts.googleapis.com/css2?family=Jost:wght@400;500;600;700&family=Lato:wght@400;700&display=swap">
<style>
  :root {
    --bg: #2a2a2c;
    --card-white: #f4f4f6;
    --card-white-edge: #e2e2e8;
    --purple: #3a2275;
    --purple-deep: #2a1659;
    --purple-text: #3d3070;
    --orange: #f0931e;
    --white: #ffffff;
    --ring: #d9d9de;
  }
  * { box-sizing: border-box; margin: 0; padding: 0; }
  html, body { width: 1200px; height: 997px; overflow: hidden; }
  body {
    background: var(--bg);
    font-family: "Lato", sans-serif;
    position: relative;
  }
  .card {
    position: absolute;
    left: 300px;
    width: 600px;
    height: 366px;
    border-radius: 18px;
    overflow: hidden;
    box-shadow: 0 14px 34px rgba(0,0,0,.45);
  }
  /* Front side */
  .card--front {
    top: 70px;
    background: linear-gradient(135deg, var(--card-white) 0%, var(--card-white-edge) 100%);
  }
  .front__headline {
    position: absolute;
    left: 0; right: 0; top: 78px;
    text-align: center;
    font-family: "Jost", sans-serif;
    font-weight: 400;
    font-size: 40px;
    line-height: 1.15;
    letter-spacing: 1px;
    color: var(--purple-text);
    text-transform: uppercase;
  }
  .front__headline strong { color: var(--orange); font-weight: 700; }
  .front__brand {
    position: absolute;
    left: 0; right: 0; top: 222px;
    text-align: center;
  }
  .brand-name {
    font-family: "Jost", sans-serif;
    font-weight: 500;
    font-size: 46px;
    letter-spacing: .5px;
    line-height: 1;
  }
  .front__brand .brand-name { color: var(--purple-text); }
  .brand-tagline {
    margin-top: 8px;
    font-family: "Jost", sans-serif;
    font-size: 13px;
    letter-spacing: 3px;
    color: var(--orange);
  }
  /* Back side */
  .card--back {
    top: 520px;
    background: linear-gradient(135deg, var(--purple) 0%, var(--purple-deep) 100%);
    color: var(--white);
  }
  .back__brand {
    position: absolute;
    left: 40px; top: 54px;
  }
  .back__brand .brand-name { color: var(--white); font-size: 50px; }
  .back__band {
    position: absolute;
    left: 0; right: 0; top: 150px;
    height: 50px;
    background: var(--orange);
  }
  .back__name {
    position: absolute;
    left: 40px; top: 160px;
    font-size: 22px;
    color: var(--white);
  }
  .back__name b { font-weight: 700; }
  .back__name .divider {
    display: inline-block;
    width: 3px; height: 24px;
    background: var(--purple-deep);
    margin: 0 8px;
    vertical-align: -4px;
  }
  .back__photo {
    position: absolute;
    right: 32px; top: 40px;
    width: 196px; height: 196px;
    border-radius: 50%;
    border: 7px solid var(--ring);
    background: radial-gradient(circle at 50% 40%, #e6e6ea 0%, #c7c8ce 55%, #2b3150 100%);
  }
  .back__abn {
    position: absolute;
    right: 36px; top: 258px;
    font-size: 15px;
    letter-spacing: .5px;
  }
  .back__contact {
    position: absolute;
    left: 40px; top: 240px;
    list-style: none;
    font-size: 18px;
    line-height: 1.75;
  }
  .back__contact .label { color: var(--orange); font-weight: 700; margin-right: 8px; }
  .back__web { letter-spacing: 4px; }
  .back__web span { color: var(--orange); }
</style>
</head>
<body>
  <section class="card card--front" aria-label="Business card front">
    <h1 class="front__headline">Looking for <strong>best deals</strong><br>in property ?</h1>
    <div class="front__brand">
      <div class="brand-name">calvanto group</div>
      <div class="brand-tagline">BUY | SELL | RENT</div>
    </div>
  </section>

  <section class="card card--back" aria-label="Business card back">
    <div class="back__brand"><div class="brand-name">calvanto group</div></div>
    <div class="back__band"></div>
    <p class="back__name"><b>Daniel Tran</b><span class="divider"></span>Director</p>
    <div class="back__photo" role="img" aria-label="Head shot photo of the director in a dark suit"></div>
    <p class="back__abn">ABN:12 345 678 901</p>
    <ul class="back__contact">
      <li><span class="label">M:</span>0412-555-308</li>
      <li><span class="label">E:</span>daniel.tran@calvanto.com.au</li>
      <li class="back__web">www.<span>calvanto</span>.com.au</li>
    </ul>
  </section>
</body>
</html>
```